Business Card Design & Gift cards, Gift Cert, Donation Card

Retail Gift Store-in addition to Business Cards we'd like sequenced 2 sided Gift cards, Gift Certificate Cards, and Donation Cards.please see examples and email for clarificationlogos attached with examples-
Gift Card, Gift Certificate and Donation Card will all be same style just differant upper right title, with back side info as example.
business card, as example is single sided.
looking for additional ideas for layout

Industry/Entity Type

Business

Contact Information for Business Card

211 Newman St.East Tawas, MI 48730989.362.8730Office@BrewKrew.com

Requirements
Must have
• Blue as per example
• Logos provided
• like gradiant background

```html
<!DOCTYPE html>
<html lang="en">
<head>
<meta charset="utf-8">
<title>Tillow Marsh – Business Card &amp; Gift Card</title>
<link rel="stylesheet" href="https://fonts.googleapis.com/css2?family=Comic+Neue:wght@400;700&display=swap">
<style>
  :root {
    --stage: #e9e9e9;
    --card: #ffffff;
    --ink: #1c1c1c;
    --ink-soft: #4a4a4a;
    --rule: #3a3a3a;
    --brand-blue: #0a2fd0;
    --sun-yellow: #f7e21a;
    --night: #000000;
    --ghost-blue: #e8ecfa;
    --ghost-yellow: #fbf6dc;
  }
  * { box-sizing: border-box; margin: 0; padding: 0; }
  html, body { width: 1105px; height: 1200px; overflow: hidden; }
  body {
    background: var(--stage);
    font-family: "Comic Neue", "Comic Sans MS", cursive;
    color: var(--ink);
    position: relative;
  }
  .card {
    position: absolute;
    left: 196px;
    width: 720px;
    background: var(--card);
    border-radius: 25px;
    overflow: hidden;
    box-shadow: 0 3px 8px rgba(0,0,0,0.25);
  }
  .card--front { top: 145px; height: 413px; }
  .card--back  { top: 604px; height: 409px; }

  .artwork { position: absolute; left: 0; top: 0; width: 384px; height: 413px; }

  .brand-name {
    position: absolute; left: 394px; top: 40px;
    width: 300px;
    font-size: 35px; font-weight: 400; letter-spacing: 0;
    line-height: 52px;
    color: var(--ink); white-space: nowrap;
  }
  .contact, .services {
    position: absolute; left: 394px;
    list-style: none;
    font-size: 21px; line-height: 26.5px;
    color: var(--ink-soft);
  }
  .contact { top: 120px; }
  .services { top: 275px; }
  .contact li { display: flex; align-items: center; gap: 6px; }
  .contact svg { width: 16px; height: 16px; fill: var(--ink); flex: none; }

  .back-decor { position: absolute; left: 236px; top: 30px; width: 270px; height: 345px; }
  .card-number {
    position: absolute; right: 40px; top: 36px;
    font-size: 18px; color: var(--ink);
  }
  .field {
    position: absolute; display: flex; align-items: flex-end;
  }
  .field__label { white-space: nowrap; }
  .field__line { flex: 1; border-bottom: 1.5px solid var(--rule); height: 1px; margin-bottom: 6px; }
  .field--large { font-size: 26px; left: 57px; width: 610px; gap: 24px; }
  .field--small { font-size: 22px; left: 55px; width: 622px; gap: 8px; }
  .field--to { top: 77px; }
  .field--from { top: 135px; }
  .field--issued { top: 217px; }
  .field--expires { top: 265px; }
  .field--employee { top: 313px; }
  .field--employee .field__label { margin-right: 14px; }
</style>
</head>
<body>

  <section class="card card--front" aria-label="Business card front">
    <svg class="artwork" viewBox="0 0 384 413" role="img" aria-label="Illustration of a dancing figure stepping over a rising yellow sun, blue on black">
      <defs>
        <linearGradient id="art-fill" x1="0" y1="0" x2="0" y2="1">
          <stop offset="0" stop-color="#2a4be0"/>
          <stop offset="0.65" stop-color="#0a2fd0"/>
          <stop offset="1" stop-color="#f7e21a"/>
        </linearGradient>
      </defs>
      <rect x="0" y="0" width="70" height="413" fill="var(--night)"/>
      <rect x="70" y="0" width="314" height="413" fill="url(#art-fill)" opacity="0.85"/>
    </svg>

    <div class="brand-name">TILLOW MARSH</div>

    <ul class="contact">
      <li>482 Larkfield Ave.</li>
      <li>Pine Hollow, MI 48731</li>
      <li><svg viewBox="0 0 16 16" aria-hidden="true"><path d="M3 1.5l3 .5 1 3.5-2 1.2a8 8 0 0 0 4.3 4.3L10.5 9l3.5 1 .5 3-2 2C6.5 15 1 9.5 1 3.5z"/></svg>989.517.4296</li>
      <li><svg viewBox="0 0 16 16" aria-hidden="true"><path d="M1 3h14v10H1z M1.5 3.5L8 9l6.5-5.5" stroke="#fff" stroke-width="1.2"/></svg>Office@TillowMarsh.com</li>
      <li><svg viewBox="0 0 16 16" aria-hidden="true"><circle cx="8" cy="8" r="7"/><path d="M5 4c2 1 1 3 3 3s1 3 3 4" stroke="#fff" stroke-width="1.4" fill="none"/></svg>www.TillowMarsh.com</li>
    </ul>

    <ul class="services">
      <li>Gourmet Food</li>
      <li>Fine Wines | Gift Baskets</li>
      <li>Kitchen &amp; Bath Accessories</li>
      <li>Candles | Cards | Soaps</li>
    </ul>
  </section>

  <section class="card card--back" aria-label="Gift card back">
    <svg class="back-decor" viewBox="0 0 270 345" role="img" aria-label="Faint background illustration of the dancing figure and sun">
      <defs>
        <linearGradient id="ghost-fill" x1="0" y1="0" x2="0" y2="1">
          <stop offset="0" stop-color="var(--ghost-blue)"/>
          <stop offset="0.75" stop-color="var(--ghost-blue)"/>
          <stop offset="1" stop-color="var(--ghost-yellow)"/>
        </linearGradient>
      </defs>
      <rect x="0" y="0" width="270" height="345" rx="20" fill="url(#ghost-fill)" opacity="0.7"/>
    </svg>

    <div class="card-number">Card Number : 58724</div>

    <div class="field field--large field--to"><span class="field__label">To :</span><span class="field__line"></span></div>
    <div class="field field--large field--from"><span class="field__label">Form :</span><span class="field__line"></span></div>
    <div class="field field--small field--issued"><span class="field__label">Date&nbsp; Issued :</span><span class="field__line"></span></div>
    <div class="field field--small field--expires"><span class="field__label">Expiration Date :</span><span class="field__line"></span></div>
    <div class="field field--small field--employee"><span class="field__label">Employee :</span><span class="field__line"></span></div>
  </section>

</body>
</html>
```